help me Create Tovaro Kitchen offsite menus

I need something vibrant and it needs some pictures to go with the food i will include the logo of the location and the menu. it is for offsite catering to be delivered to venues in our local town, we are currently catering in house only but are expanding to do delivery so need something that i can use as a menu. the file needs to be able to be edited

Target Market(s)

local small businesses that require catering for their group lunches

Industry/Entity Type

Catering

Font styles to use
Serif
Decorative

Requirements
Must have
• colour and soul, must have a good feeling and be happy
Nice to have
• some other stock photos of the described products
Should not have
• not be too corporate and businessy

```html
<!DOCTYPE html>
<html lang="en">
<head>
<meta charset="utf-8">
<title>Tovaro Kitchen – Offsite Catering Menu</title>
<link rel="stylesheet" href="https://fonts.googleapis.com/css2?family=Berkshire+Swash&family=Oswald:wght@300;400&display=swap">
<style>
:root{
  --backdrop:#e7e2da;
  --card:#121a22;
  --card-edge:#1d2731;
  --logo-disc:#14293d;
  --orange:#e8742b;
  --orange-dark:#b9561c;
  --ink:#e9e6df;
  --ink-soft:#b7b4ad;
  --rule:#d9c21f;
  --rule-white:#e9e6df;
}
*{box-sizing:border-box;margin:0;padding:0}
html,body{width:1200px;height:754px;overflow:hidden}
body{background:var(--backdrop);position:relative;font-family:"Oswald",sans-serif;color:var(--ink)}
.menu-card{position:absolute;top:20px;width:550px;height:714px;background:var(--card);
  clip-path:polygon(22px 0,528px 0,550px 22px,550px 692px,528px 714px,22px 714px,0 692px,0 22px);}
.menu-card::before{content:"";position:absolute;inset:8px;border:1px solid var(--card-edge);
  clip-path:polygon(16px 0,calc(100% - 16px) 0,100% 16px,100% calc(100% - 16px),calc(100% - 16px) 100%,16px 100%,0 calc(100% - 16px),0 16px);}
.card-platter{left:35px}
.card-tea{left:615px}
.abs{position:absolute}
.brand-disc{position:absolute;border-radius:50%;background:var(--logo-disc);display:flex;align-items:center;justify-content:center;gap:6px}
.brand-name{font-family:"Berkshire Swash",serif;color:var(--ink);line-height:1;text-align:center}
.brand-dot{width:10px;height:10px;border-radius:50%;background:var(--orange)}
.photo{position:absolute}
.ribbon{position:absolute}
.ribbon svg{position:absolute;inset:0;width:100%;height:100%}
.ribbon-title{position:relative;display:flex;align-items:center;justify-content:center;height:100%;
  font-family:"Berkshire Swash",serif;color:var(--ink);letter-spacing:.5px}
.item{position:absolute;font-weight:300;font-size:11.5px;text-transform:uppercase;letter-spacing:.4px;white-space:nowrap}
.item small{display:block;font-size:7px;color:var(--ink-soft);letter-spacing:.3px;margin-top:2px}
.price{position:absolute;font-weight:300;font-size:11.5px;text-transform:uppercase;white-space:nowrap;letter-spacing:.3px}
.price small{display:block;font-size:7px;color:var(--ink-soft)}
.rule{position:absolute;width:1.5px}
.lunch-heading{font-weight:300;font-size:15px;letter-spacing:.6px}
.lunch-copy{position:absolute;font-family:"Berkshire Swash",serif;font-size:9.5px;line-height:15px;text-align:center;letter-spacing:.3px}
.contact-phone{position:absolute;display:flex;align-items:center;gap:8px;font-size:15px;font-weight:300;letter-spacing:.5px}
.contact-note{position:absolute;font-size:9px;font-weight:300;letter-spacing:.2px}
</style>
</head>
<body>

<!-- Platter & lunch side -->
<section class="menu-card card-platter">
  <div class="brand-disc" style="left:41px;top:22px;width:116px;height:116px">
    <span class="brand-name" style="font-size:17px">Tovaro<br>Kitchen</span>
    <span class="brand-dot"></span>
  </div>
  <div class="photo" role="img" aria-label="Sliced red capsicum ring" style="left:220px;top:40px;width:72px;height:66px;border-radius:50%;background:radial-gradient(circle,#1a0f10 30%,#d62b1c 34%,#a11812 60%,transparent 63%)"></div>
  <div class="photo" role="img" aria-label="Whole red chilli pepper" style="left:392px;top:26px;width:112px;height:110px;border-radius:48% 52% 45% 55%;background:radial-gradient(circle at 40% 40%,#e83a24,#9c140c 70%)"></div>

  <div class="ribbon" style="left:50px;top:143px;width:467px;height:33px">
    <svg viewBox="0 0 467 33" preserveAspectRatio="none"><polygon points="0,2 467,0 452,17 467,33 0,31 14,16" fill="var(--orange)"/></svg>
    <div class="ribbon-title" style="font-size:17px">Platter menu</div>
  </div>

  <div class="item" style="left:71px;top:204px">Hot finger food platter (chef's choice 60 pieces)</div>
  <div class="price" style="left:440px;top:204px">$105.00</div>
  <div class="item" style="left:71px;top:228px">Hot roast buffet platter pork or beef with roast vegetables<small>&amp; one grazing salad minimum 10 guests</small></div>
  <div class="price" style="left:440px;top:228px">$16.50PP</div>
  <div class="item" style="left:71px;top:264px">Sandwich box (10 rounds)</div>
  <div class="price" style="left:446px;top:264px">$60.00</div>
  <div class="item" style="left:71px;top:289px">Medium bread roll platter 15 medium size lunch rolls</div>
  <div class="price" style="left:446px;top:289px">$75.00</div>
  <div class="item" style="left:71px;top:315px">Large meat and salad rolls<small>(choice of chicken, chicken schnitzel, roast beef, ham)</small></div>
  <div class="price" style="left:430px;top:315px">$9.00 each</div>
  <div class="item" style="left:71px;top:355px">Wraps<small>(choice of chicken, chicken schnitzel, roast beef, ham)</small></div>
  <div class="price" style="left:430px;top:355px">$7.50 each</div>
  <div class="item" style="left:71px;top:395px">Individual salad bowls - caesar, greek, creamy pasta, seafood<small>add chicken or grilled chicken schnitzel</small></div>
  <div class="price" style="left:452px;top:395px">$9.50<small>$3.50</small></div>
  <div class="item" style="left:71px;top:439px">Large grazing salads - add one to a sandwich platter<small>or hot finger food platter add a healthy side for your group (serves 10)</small></div>
  <div class="price" style="left:446px;top:439px">$35.00</div>
  <div class="item" style="left:71px;top:476px">Pizza, pasta and salad (minimum 8 guests)</div>
  <div class="price" style="left:436px;top:476px">$19.00PP</div>
  <div class="rule" style="left:488px;top:200px;height:292px;background:var(--rule)"></div>

  <div class="photo" role="img" aria-label="Grazing table with sandwiches and salads" style="left:27px;top:511px;width:160px;height:160px;border-radius:50%;background:radial-gradient(circle at 55% 55%,#c9a46a,#6e5a44 55%,#2b2a2a 100%)"></div>

  <div class="ribbon" style="left:197px;top:522px;width:302px;height:43px">
    <svg viewBox="0 0 302 43" preserveAspectRatio="none"><polygon points="0,3 302,0 288,21 302,43 0,40 14,21" fill="var(--orange)"/></svg>
    <div class="ribbon-title" style="font-size:21px">Lunch</div>
  </div>
  <div class="item lunch-heading" style="left:226px;top:576px">Gazing table minimum 5</div>
  <div class="item lunch-heading" style="left:440px;top:576px">$16.50 PP</div>
  <p class="lunch-copy" style="left:195px;top:606px;width:310px">Make your own sandwich buffet for guests to make their own sandwich from a variety of breads and fillings with tea and coffee facilities.</p>

  <div class="contact-phone" style="left:412px;top:645px">
    <svg width="12" height="12" viewBox="0 0 24 24" aria-hidden="true"><circle cx="12" cy="12" r="11" fill="none" stroke="var(--ink)" stroke-width="1.5"/><path d="M8 6.5l2 2-1 1.5c.8 1.8 2.2 3.2 4 4l1.5-1 2 2-1.5 2c-4 0-8.5-4.5-8.5-8.5z" fill="var(--ink)"/></svg>
    <span>55 410 820</span>
  </div>
  <p class="contact-note" style="left:130px;top:672px">To book in your event call us Now on 55 410 820 or go to www.tovarokitchen.com.au</p>
</section>

<!-- Tea, coffee & morning tea side -->
<section class="menu-card card-tea">
  <div class="photo" role="img" aria-label="Stack of chocolate chip cookies" style="left:47px;top:64px;width:218px;height:93px;border-radius:46% 54% 50% 50%;background:radial-gradient(ellipse at 60% 45%,#d7924a,#a45e26 70%,transparent 72%)"></div>
  <div class="brand-disc" style="left:306px;top:17px;width:188px;height:188px">
    <span class="brand-name" style="font-size:26px">Tovaro<br>Kitchen</span>
    <span class="brand-dot" style="width:14px;height:14px"></span>
  </div>

  <div class="ribbon" style="left:49px;top:216px;width:206px;height:26px">
    <svg viewBox="0 0 206 26" preserveAspectRatio="none"><polygon points="0,0 206,2 196,13 206,26 0,24 10,12" fill="var(--orange)"/></svg>
    <div class="ribbon-title" style="font-size:13px">Tea &amp; Coffee</div>
  </div>
  <div class="item" style="left:70px;top:264px;font-size:10px">Tea and coffee station<small style="font-size:5px">continuous tea and coffee station for your day</small></div>
  <div class="price" style="left:212px;top:264px;font-size:9.5px">$3.00PP<small style="font-size:5px">$3.00PP</small></div>
  <div class="item" style="left:70px;top:291px;font-size:10px">Barrista delivered<small style="font-size:5px">(pre order only)</small></div>
  <div class="price" style="left:198px;top:291px;font-size:9.5px">$5.50 each</div>
  <div class="rule" style="left:257px;top:262px;height:35px;background:var(--rule-white)"></div>

  <div class="ribbon" style="left:49px;top:330px;width:206px;height:24px">
    <svg viewBox="0 0 206 24" preserveAspectRatio="none"><polygon points="0,0 206,2 196,12 206,24 0,22 10,11" fill="var(--orange)"/></svg>
    <div class="ribbon-title" style="font-size:13px">Extra</div>
  </div>
  <div class="item" style="left:70px;top:371px;font-size:10px">Juice 2 lt bottle</div>
  <div class="price" style="left:198px;top:371px;font-size:9.5px">$5.95</div>
  <div class="rule" style="left:257px;top:374px;height:9px;background:var(--rule-white)"></div>

  <div class="photo" role="img" aria-label="Venue interior with catering spread on a table" style="left:298px;top:216px;width:192px;height:173px;background:linear-gradient(180deg,#6d7778 0%,#9fa6a2 35%,#5a4b3a 60%,#b98a4f 100%)"></div>

  <div class="ribbon" style="left:49px;top:413px;width:454px;height:32px">
    <svg viewBox="0 0 454 32" preserveAspectRatio="none"><polygon points="0,0 454,2 440,17 454,32 0,30 14,15" fill="var(--orange)"/></svg>
    <div class="ribbon-title" style="font-size:16px">Morning or Afternoon Tea</div>
  </div>

  <div class="item" style="left:114px;top:464px">Scones and slices platter</div>
  <div class="price" style="left:343px;top:464px">$6.50 per person</div>
  <div class="item" style="left:114px;top:491px">Muffins</div>
  <div class="price" style="left:343px;top:491px">$5.00 per person</div>
  <div class="item" style="left:114px;top:521px">Homemade biscuits</div>
  <div class="price" style="left:343px;top:521px">$4.50 per person</div>
  <div class="item" style="left:114px;top:547px">Banana bread</div>
  <div class="price" style="left:343px;top:547px">$6.00 per person</div>
  <div class="item" style="left:114px;top:580px">Gluten free frittata</div>
  <div class="price" style="left:343px;top:580px">$5.50 per person</div>
  <div class="item" style="left:114px;top:607px">Ploughmans platter</div>
  <div class="price" style="left:343px;top:607px">$8.50 per person</div>
  <div class="item" style="left:114px;top:637px">Whole fresh fruit platter</div>
  <div class="price" style="left:343px;top:637px">$45.00 per platter</div>
  <div class="item" style="left:114px;top:665px">Chopped fresh seasonal fruit platter</div>
  <div class="price" style="left:343px;top:665px">$49.50 per platter</div>
  <div class="rule" style="left:457px;top:465px;height:208px;background:var(--rule-white)"></div>
</section>

</body>
</html>
```